Plenko - Shoe Fitting App : Foot scanning app, 3D reconstruction and Fit recommandation.

We are a startup that has developed a 3D scanning App that compares the 3d reconstructed foot to the 3D Last (mould) of a shoe to find the best match and recommend a shoe size with a graphical representation of the fit on a reconstructed foot without texturing. The challenge of this app is to have a simple and intuitive onboarding of the user with clean and crisp ui and a simple tutorial for foot scanning. 3D representation of the fit is also key. What you see is what you feel is what we would like to achieve.

Target Market(s)

Sneaker Brands and athletic shoes brands

Industry/Entity Type

Footwear

Font styles to use
Other font styles liked:
• Oswald or Droid Serif

Colors
0094D4
00A9DD
6FCCEA
C7EBF8
E9F6FB

Requirements
Must have
• Simple intuitive UI to onboard the customer to scan his bare foot (please look at attached image on how to scan the foot). You must flip your phone so that the screen is facing your foot. Start at 40cm distance form the front of your foot and turn 360% slowly to capture the foot while you feel the aptic of the iPhone. That needs to be presented with a simple animation that the user can easily understand and skip if he is a returning customer and knows how to do that. the rest of the UI is to present the result of the scanned foot for the user to use to get his fit and size. The other must have is the final result screen. Where the user will a representation of the foot (snug, loose ) of different predefined areas of the foot so he can choose the fit that he likes and not necessarily the size that we suggest. Must match website design (https://www.plenko.example)
Nice to have
• An animation of the whole process (scan-compare 3d foot with 3d shoe last(or mould) and get the 3D result of the best fit + associated size. Optionaly, an option to play with your foot and transform it (avatar like with accessories and colours)
Should not have
• Too many colours. Too much text. No gender type. No race type.

```html
<!DOCTYPE html>
<html lang="en">
<head>
<meta charset="utf-8">
<title>Plenko – Foot Scan Onboarding</title>
<link href="https://fonts.googleapis.com/css2?family=Roboto:wght@400;500;700;900&display=swap" rel="stylesheet">
<style>
  :root{
    --backdrop:#5c5c5c;
    --screen:#050505;
    --card:#121212;
    --card-edge:#2a2a2a;
    --panel:#1a1a1a;
    --teal:#4ab5b5;
    --white:#ffffff;
    --muted:#e2e2e2;
    --track:#2e2e2e;
    --mesh-light:#c9c9c9;
    --mesh-dark:#3a3a3a;
    --skin-light:#d8a88e;
    --skin-dark:#9a6a55;
  }
  *{box-sizing:border-box;margin:0;padding:0}
  html,body{width:1200px;height:528px;overflow:hidden}
  body{background:var(--backdrop);font-family:"Roboto",Arial,sans-serif;color:var(--white);position:relative}
  .screen{position:absolute;top:65px;width:180px;height:398px;border-radius:18px;background:var(--screen);overflow:hidden}
  .screen > *{position:absolute}
  .status{top:10px;left:15px;right:15px;display:flex;justify-content:space-between;align-items:center;font-size:6px;font-weight:500}
  .status-icons{display:flex;gap:4px;align-items:center}
  .brand{top:28px;left:0;right:0;text-align:center;font-size:24px;font-weight:900;letter-spacing:.5px}
  .card{top:67px;left:15px;width:151px;height:374px;border-radius:10px;background:var(--card);border:1px solid var(--card-edge)}
  .screen .card{height:374px}
  .head-box{left:24px;width:132px;top:75px;height:78px;border-radius:8px;background:var(--panel);text-align:center;padding:10px 4px 0}
  .title{font-size:9.6px;font-weight:500;line-height:11.5px}
  .title.caps{text-transform:uppercase}
  .body{font-size:6.6px;line-height:9.6px;margin-top:5px;color:var(--muted)}
  .art{border-radius:10px}
  .art.mesh{background:linear-gradient(180deg,var(--mesh-light) 0%,#8a8a8a 45%,var(--mesh-dark) 100%);opacity:.55}
  .art.skin{background:linear-gradient(200deg,var(--skin-light) 0%,var(--skin-dark) 100%);opacity:.8}
  .dots{top:309px;left:0;right:0;display:flex;justify-content:center;gap:4px}
  .dots i{width:5px;height:5px;border:1px solid var(--white);border-radius:1px}
  .dots i.on{background:var(--white)}
  .btn{left:29px;width:121px;height:16px;border-radius:8px;display:flex;align-items:center;justify-content:center;font-size:6.6px;font-weight:700;letter-spacing:.3px}
  .btn.primary{background:var(--teal);color:var(--white)}
  .btn.secondary{background:var(--white);color:#111}
  .home-bar{top:357px;left:58px;width:63px;height:1.5px;background:var(--white);border-radius:1px}
  .progress{left:36px;width:108px;height:3px;border-radius:2px;background:var(--track)}
  .progress.full{background:var(--teal)}
  .center{left:0;right:0;text-align:center}
  .teal-box{left:25px;width:130px;background:var(--teal);border-radius:4px;text-align:center}
  .badge-360{left:27px;top:243px;width:22px;height:22px;border-radius:50%;background:var(--white);color:#111;font-size:5.5px;font-weight:700;display:flex;align-items:center;justify-content:center}
  .choice{width:13px;height:13px;border-radius:50%;font-size:3px;display:flex;align-items:center;justify-content:center}
  .choice.filled{background:#fff;color:#111}
  .choice.outline{border:1px solid #fff}
</style>
</head>
<body>

<!-- Screen 1: lighting -->
<section class="screen" style="left:60px">
  <div class="status"><span>9:41</span><span class="status-icons"><svg width="6" height="5"><path d="M0 5h6V0z" fill="#fff"/></svg><svg width="6" height="5"><path d="M0 2a4.5 4.5 0 0 1 6 0L3 5z" fill="#fff"/></svg><svg width="7" height="4"><rect x=".5" y=".5" width="5.5" height="3" rx=".5" fill="none" stroke="#fff"/><rect x="1.5" y="1.5" width="3.5" height="1" fill="#fff"/></svg></span></div>
  <div class="brand">Plenko</div>
  <div class="card"></div>
  <div class="head-box">
    <p class="title">Make Sure You're in<br>A Well Lit Area</p>
    <p class="body">Avoid strong light from only one<br>direction. This casts deep shadows<br>that reduce accuracy of the scan.</p>
  </div>
  <div class="art mesh" role="img" aria-label="Wireframe 3D feet standing side by side" style="left:41px;top:187px;width:91px;height:86px"></div>
  <div class="dots"><i class="on"></i><i></i><i></i></div>
  <div class="btn primary" style="top:325px">NEXT</div>
  <div class="home-bar"></div>
</section>

<!-- Screen 2: shoes off -->
<section class="screen" style="left:285px">
  <div class="status"><span>9:41</span><span class="status-icons"><svg width="6" height="5"><path d="M0 5h6V0z" fill="#fff"/></svg><svg width="6" height="5"><path d="M0 2a4.5 4.5 0 0 1 6 0L3 5z" fill="#fff"/></svg><svg width="7" height="4"><rect x=".5" y=".5" width="5.5" height="3" rx=".5" fill="none" stroke="#fff"/><rect x="1.5" y="1.5" width="3.5" height="1" fill="#fff"/></svg></span></div>
  <div class="brand">Plenko</div>
  <div class="card"></div>
  <div class="head-box">
    <p class="title">Take Off Your Shoes<br>and Roll Up Pants</p>
    <p class="body">To scan your feet, the camera<br>needs to see the unique details,<br>including your ankle.</p>
  </div>
  <div class="art mesh" role="img" aria-label="Wireframe bare feet with removed sneakers and socks beside them" style="left:27px;top:175px;width:130px;height:122px"></div>
  <div class="dots"><i></i><i class="on"></i><i></i></div>
  <div class="btn primary" style="top:325px">NEXT</div>
  <div class="home-bar"></div>
</section>

<!-- Screen 3: flip screen -->
<section class="screen" style="left:510px">
  <div class="status"><span>9:41</span><span class="status-icons"><svg width="6" height="5"><path d="M0 5h6V0z" fill="#fff"/></svg><svg width="6" height="5"><path d="M0 2a4.5 4.5 0 0 1 6 0L3 5z" fill="#fff"/></svg><svg width="7" height="4"><rect x=".5" y=".5" width="5.5" height="3" rx=".5" fill="none" stroke="#fff"/><rect x="1.5" y="1.5" width="3.5" height="1" fill="#fff"/></svg></span></div>
  <div class="brand">Plenko</div>
  <div class="card"></div>
  <div class="head-box" style="height:58px;padding-top:11px">
    <p class="title caps">Flip the screen<br>towards your toes<br>to start scanning</p>
  </div>
  <div class="art mesh" role="img" aria-label="Wireframe 3D foot with a 40 cm scanning path around it" style="left:49px;top:149px;width:90px;height:117px"></div>
  <div class="badge-360">360°</div>
  <div class="dots"><i></i><i></i><i class="on"></i></div>
  <div class="btn primary" style="top:325px">LEFT FOOT</div>
  <div class="home-bar"></div>
</section>

<!-- Screen 4: reconstruction check -->
<section class="screen" style="left:735px">
  <div class="status"><span>9:41</span><span class="status-icons"><svg width="6" height="5"><path d="M0 5h6V0z" fill="#fff"/></svg><svg width="6" height="5"><path d="M0 2a4.5 4.5 0 0 1 6 0L3 5z" fill="#fff"/></svg><svg width="7" height="4"><rect x=".5" y=".5" width="5.5" height="3" rx=".5" fill="none" stroke="#fff"/><rect x="1.5" y="1.5" width="3.5" height="1" fill="#fff"/></svg></span></div>
  <div class="brand">Plenko</div>
  <div class="card"></div>
  <div class="head-box" style="height:58px;padding-top:11px">
    <p class="title">Please check that the<br>reconstruction of your<br>foot seems correct</p>
  </div>
  <div class="art skin" role="img" aria-label="Reconstructed 3D bare foot, side view" style="left:40px;top:177px;width:91px;height:80px"></div>
  <svg style="left:27px;top:290px" width="10" height="7" viewBox="0 0 10 7"><path d="M0 3.5C2 0 8 0 10 3.5 8 7 2 7 0 3.5z" fill="var(--teal)"/><circle cx="5" cy="3.5" r="1.5" fill="#000"/></svg>
  <div class="btn secondary" style="top:305px">SCAN AGAIN</div>
  <div class="btn primary" style="top:325px">MY FIT</div>
  <div class="home-bar"></div>
</section>

<!-- Screen 5: loading data -->
<section class="screen" style="left:960px">
  <div class="status"><span>9:41</span><span class="status-icons"><svg width="6" height="5"><path d="M0 5h6V0z" fill="#fff"/></svg><svg width="6" height="5"><path d="M0 2a4.5 4.5 0 0 1 6 0L3 5z" fill="#fff"/></svg><svg width="7" height="4"><rect x=".5" y=".5" width="5.5" height="3" rx=".5" fill="none" stroke="#fff"/><rect x="1.5" y="1.5" width="3.5" height="1" fill="#fff"/></svg></span></div>
  <div class="brand">Plenko</div>
  <div class="card"></div>
  <div class="head-box" style="height:72px;padding-top:10px">
    <p class="title">Loading Your Data</p>
    <p class="body" style="margin-top:4px">This process might take a few<br>minutes</p>
    <p style="font-size:6px;font-weight:700;color:var(--teal);margin-top:3px">0%</p>
  </div>
  <div class="progress" style="top:136px"></div>
  <div class="center" style="top:156px">
    <p style="font-size:6.6px;font-weight:700">FUN FACTS ABOUT FEET</p>
    <p style="font-size:4.4px;line-height:7.6px;margin-top:3px">Our feet have nearby a Quater of all bones in our<br>bodies-each one has 26 bones.</p>
    <p style="font-size:4.4px;line-height:7.6px;margin-top:1px">Feet grow as we age - our arch may flatten,<br>causing our foot size to increase.</p>
  </div>
  <div class="teal-box" style="top:206px;height:61px;padding-top:4px">
    <p style="font-size:6.4px;font-weight:700">TELL US YOUR PREFERENCE</p>
    <p style="font-size:4.4px;margin-top:2px">How do you prefer the cushion?</p>
    <div style="display:flex;justify-content:center;gap:3px;margin-top:4px">
      <span class="choice filled">Soft</span>
      <span class="choice outline">Medium</span>
      <span class="choice filled">Hard</span>
    </div>
    <p style="font-size:4.4px;line-height:9.6px;margin-top:2px">Select an option to go to the next personal<br>preference setting</p>
  </div>
  <div class="center" style="top:281px;font-size:6.4px;font-weight:700">YOU'RE ALL MEASURED UP</div>
  <div class="center" style="top:293px;font-size:6px;font-weight:700">100%</div>
  <div class="progress full" style="top:302px"></div>
  <div class="teal-box" style="top:318px;height:27px;padding:3px 6px;font-size:4.4px;line-height:7.6px">Click below to see how this shoe fits. Now that you're scanned, you can quickly try other shoes without going through the process again.</div>
  <div class="btn secondary" style="top:348px;left:29px">SEE RESULTS</div>
</section>

</body>
</html>
```